PeakRoamJourneys

1. Can you describe what your company does?

Please find enclosed documents for your reference about our business doing.

2. Who are your target customers for the website?

Company Positioning: A comprehensive supplier of premier international sports travel and high-end event services.
Core Advantage: Exclusive international partnership resources and an Official Ticketing Assurance System.
Service Standard: One-Stop, High-Quality Service Solutions based on the "An once-in-a-lifetime experience" philosophy.

Our target customers for the website:
Mid-to-High-end Sports Enthusiasts
Corporate Clients
Sports Associations
Please kindly find enclosed for more details about our target customers, I think it's very important to make it clear to you.

3. Do you have an existing domain name / website address?

Yes, I have. I just applied for this new domain and it's totally a new website. www.peakroamjourneys.example

4. In addition to a Home Page, which other pages / sections would you like your website to have:
About Us
Contact Us , Office / Mailing Address
Sports Travel Products( Bucket Lists) : Globe Shield, Royal Quartet, Vantara Games, Football, KHL, Golf, Skiing, Hiking,Galas
Reviews/ Unforgettable Moments
FAQs
Any other page / section you would like: Here is the website for your reference, www.lanewander.example
For each of the pages / sections you’d like to have, please provide the text (and images, if available) you would like to include.
Please recommend 2-3 templates to me, and let me know what kind of text I will provide to every web pages.

5. Which of the below are features and functionalities your website will need:
Image Gallery
Videos
Contact Form
Maps
FAQs
6. Please provide the URLs for the social media profiles you'd like to link to the website.

Do you know Bright Lantern App?

Please let me know anything you need, thank you very much!

Have a good day!

Target Market(s)

Travel for the world-wide sports games and make an once-in-a-lifetime experience

Industry/Entity Type

sports and travel industry

Coding

Number of Pages Required

5+ page

Requirements
Must have
• our logo
Nice to have
• On the homepage, I’d like a banner-style section to prominently showcase the latest products.

```html
<!DOCTYPE html>
<html lang="en">
<head>
<meta charset="utf-8">
<title>PeakRoamJourneys – The Ultimate in Sports Travel</title>
<link href="https://fonts.googleapis.com/css2?family=Roboto+Slab:wght@700;800;900&family=Roboto:wght@400;500;700;900&display=swap" rel="stylesheet">
<style>
:root{
  --red:#e2231a;
  --blue:#0d3f8d;
  --blue-deep:#0a3278;
  --blue-panel:#1e56a8;
  --navy:#1a2550;
  --ink:#222;
  --field:#ececec;
  --white:#fff;
}
*{margin:0;padding:0;box-sizing:border-box}
html,body{width:1200px;height:5190px;overflow:hidden}
body{font-family:"Roboto",Arial,Helvetica,sans-serif;color:var(--ink);background:var(--white);position:relative}
.abs{position:absolute}
section,header,footer{position:absolute;left:0;width:1200px}
.display{font-family:"Roboto Slab","Rockwell","Arial Black",sans-serif;font-weight:800;letter-spacing:.2px}
.ph{position:absolute}

/* hero */
.hero{top:0;height:640px;overflow:hidden}
.hero-bg{inset:0;background:linear-gradient(180deg,#4f8cc4 0%,#7fb0d8 40%,#c3d8e8 72%,#e9eff3 100%)}
.nav{top:0;height:74px;width:1200px}
.logo{left:107px;top:24px;font-size:20px;color:var(--blue)}
.menu{left:382px;top:29px;display:flex;gap:28px;font-size:13px;color:var(--navy)}
.menu a{text-decoration:none;color:inherit;position:relative}
.menu a.active{color:var(--red)}
.menu a.active::before{content:"";position:absolute;left:0;right:0;top:-12px;height:3px;background:var(--red)}
.quote-btn{left:930px;top:17px;width:160px;height:40px;border-radius:20px;background:var(--red);color:#fff;font-size:13px;font-weight:500;display:flex;align-items:center;justify-content:center}
.hero-title{left:145px;top:214px;font-size:56px;line-height:56px;color:#111;white-space:nowrap}
.hero-title span{color:var(--red);display:block}
.hero-sub{left:146px;top:342px;font-size:23px;color:#111}
.search{left:145px;top:388px;width:440px;height:44px;border:2px solid #333;border-radius:22px;background:rgba(255,255,255,.6);font-size:13px;color:#555;padding-left:26px;display:flex;align-items:center}
.search-btn{position:absolute;right:8px;top:7px;width:26px;height:26px;border-radius:50%;background:var(--red)}
.dots{left:570px;top:581px;display:flex;gap:12px}
.dots i{width:11px;height:11px;border-radius:50%;background:#bbb;display:block}
.dots i.on{background:var(--red)}

/* about */
.about{top:640px;height:730px}
.about-photo{left:145px;top:105px;width:274px;height:520px;background:linear-gradient(180deg,#c98a4a 0%,#6a6a4a 35%,#3f7a2e 60%,#2c5d22 100%)}
.about-video{left:326px;top:206px;width:314px;height:376px;background:#fff;padding:10px}
.about-video .ph{inset:10px;background:linear-gradient(180deg,#5d6f88 0%,#8a8f96 45%,#6c6a58 75%,#4a4a3a 100%)}
.play{left:50%;top:50%;width:50px;height:50px;margin:-25px 0 0 -25px;border-radius:50%;background:#fff}
.about h2{left:455px;top:98px;font-size:37px;line-height:44px;color:#111;white-space:nowrap}
.about-text{left:653px;top:206px;width:405px;font-size:12.4px;line-height:22px;color:#444;text-align:justify}
.about-text h4{font-size:12.4px;color:#111;font-weight:700;margin-top:18px}
.btn-red{background:var(--red);color:#fff;font-size:13px;font-weight:500;border-radius:19px;display:flex;align-items:center;justify-content:center;gap:8px}
.learn{left:653px;top:538px;width:148px;height:38px}

/* features */
.features{top:1370px;height:710px;background:radial-gradient(circle at 100% 0,#1f5fb8 0,var(--blue) 40%,var(--blue-deep) 100%)}
.features h2{top:86px;width:100%;text-align:center;color:#fff;font-size:40px}
.feature{top:159px;width:436px;height:459px;background:var(--blue-panel)}
.feature .ph{left:0;top:0;width:436px;height:216px}
.feature-box{position:absolute;left:26px;top:216px;width:384px;height:215px;background:#fff;text-align:center;padding:24px 30px}
.feature-box h3{font-size:17px;font-weight:500;color:#111}
.feature-box hr{width:40px;border:0;border-top:3px solid #222;margin:12px auto 14px}
.feature-box p{font-size:12.2px;line-height:21.5px;color:#555}

/* products */
.products{top:2080px;height:600px}
.products h2{top:78px;width:100%;text-align:center;font-size:40px;color:#111}
.circle-arrow{width:34px;height:34px;border-radius:50%;background:#e6e6e6;display:flex;align-items:center;justify-content:center}
.product{top:156px;width:284px}
.product .ph{position:relative;width:284px;height:362px}
.product p{margin-top:18px;text-align:center;font-size:17px;font-weight:700;color:#222}
.product p.hl{text-decoration:underline;text-decoration-color:var(--red);text-underline-offset:4px}

/* reviews */
.reviews{top:2680px;height:554px}
.reviews h2{top:46px;width:100%;text-align:center;font-size:40px;color:#111}
.review{top:120px;width:436px;height:330px;background:#fff;border-radius:10px;box-shadow:0 4px 22px rgba(0,0,0,.12);padding:24px 32px}
.quote-mark{width:60px;height:46px}
.review p{margin-top:14px;font-size:12.4px;line-height:24px;color:#333;text-align:justify}
.stars{color:#f08a00;font-size:13px;letter-spacing:2px;margin-top:4px}
.person{display:flex;align-items:center;gap:16px;margin-top:14px}
.avatar{width:72px;height:72px;border-radius:50%;background:linear-gradient(160deg,#c9b7a4,#6b5a4b)}
.person b{font-size:20px;font-weight:500;display:block;color:#111}
.person span{font-size:14px;color:#444}
.rev-prev{left:54px;top:290px;width:38px;height:38px;border-radius:50%;background:#e6e6e6;display:flex;align-items:center;justify-content:center}
.rev-next{left:1108px;top:290px;width:40px;height:40px;border-radius:50%;background:#111;display:flex;align-items:center;justify-content:center}

/* faq */
.faq{top:3234px;height:584px;background:linear-gradient(120deg,#e5281f 0%,var(--red) 50%,#d61f17 100%)}
.faq h2{top:92px;width:100%;text-align:center;color:#fff;font-size:40px}
.faq-item{width:444px;height:60px;border:2px solid #fff;color:#fff;font-size:14.5px;display:flex;align-items:center;justify-content:space-between;padding:0 20px}
.faq-item span:last-child{font-size:20px}

/* contact */
.contact{top:3818px;height:659px}
.contact h2{top:84px;width:100%;text-align:center;font-size:40px;color:#111}
.map{left:145px;top:154px;width:453px;height:405px;background:linear-gradient(135deg,#cfe5d8 0%,#dfeee0 40%,#e8eee6 70%,#d4e6da 100%)}
.map-card{left:20px;top:16px;width:222px;height:50px;background:#fff;font-size:13px;padding:9px 12px 0 34px;color:#222;box-shadow:0 1px 4px rgba(0,0,0,.2)}
.map-card u{font-size:11px;display:block;margin-top:3px;font-weight:500}
.field{left:624px;width:432px;height:50px;background:var(--field);font-size:13px;color:#555;padding:16px 22px}
.submit{left:626px;top:522px;width:148px;height:38px}

/* gallery */
.gallery{top:4477px;height:316px}
.g{top:0;height:316px}

/* footer */
.footer{top:4806px;height:384px;background:linear-gradient(180deg,#0d3f8d,#0a3378)}
.footer h3{font-size:18px;font-weight:700;color:#fff}
.footer ul{list-style:none;margin-top:16px}
.footer li{font-size:13px;color:#fff;line-height:22px}
.links li::before{content:"\00BB";margin-right:12px}
.nl-input{left:143px;top:120px;width:254px;height:48px;border:2px solid #fff;color:#fff;font-size:13px;display:flex;align-items:center;gap:10px;padding-left:22px}
.nl-btn{left:143px;top:180px;width:254px;height:48px;background:var(--red);color:#fff;font-size:13px;font-weight:700;display:flex;align-items:center;justify-content:center}
.touch li{display:flex;align-items:center;gap:12px;font-weight:700}
.socials{left:866px;top:200px;display:flex;gap:12px}
.socials i{width:36px;height:36px;border-radius:50%;display:block}
.copy{top:344px;width:100%;text-align:center;color:#fff;font-size:13px}
</style>
</head>
<body>

<header class="hero">
  <div class="ph hero-bg" role="img" aria-label="Hiker standing on a mountain summit above a sea of clouds"></div>
  <nav class="abs nav">
    <div class="abs logo display">PeakRoamJourneys</div>
    <div class="abs menu">
      <a class="active" href="#">Home</a><a href="#">Sports Travel</a><a href="#">Travel Advisors</a><a href="#">Guides &amp; Brochures</a><a href="#">About Us</a>
    </div>
    <div class="abs quote-btn">Get Custom Quote</div>
  </nav>
  <h1 class="abs hero-title display">The Ultimate in<span>Sports Travel</span></h1>
  <p class="abs hero-sub">Luxury Sports Travel Packages</p>
  <div class="abs search">Find your sports event
    <span class="search-btn"><svg width="26" height="26" viewBox="0 0 26 26"><circle cx="12" cy="12" r="5" fill="none" stroke="#fff" stroke-width="2"/><line x1="15.5" y1="15.5" x2="19" y2="19" stroke="#fff" stroke-width="2"/></svg></span>
  </div>
  <div class="abs dots"><i></i><i class="on"></i><i></i></div>
</header>

<section class="about">
  <div class="ph about-photo" role="img" aria-label="Golf course green at sunset"></div>
  <div class="abs about-video">
    <div class="ph" role="img" aria-label="Cricket batsman in a stadium"></div>
    <div class="abs play"><svg width="50" height="50" viewBox="0 0 50 50"><polygon points="21,18 32,25 21,32" fill="#e2231a"/></svg></div>
  </div>
  <h2 class="abs display">Premier Sports Travel and<br>Event Management Expert</h2>
  <div class="abs about-text">
    <p>Our company has been deeply rooted in the sports and high-end service sector for over a decade, with businesses covering High-end Conference Management and Planning, Sports Event Operation, and, at its core, Sports Travel services.</p>
    <h4>Professional Qualification</h4>
    <p>Holds an Outbound Travel Operating License issued by the National Tourism Administration, providing legal and reliable international travel service guarantees for clients.</p>
    <h4>Resource Advantage</h4>
    <p>Established deep partnerships with numerous large foreign sports organizations and associations to ensure clients secure scarce, official tickets for premier international events.</p>
  </div>
  <div class="abs btn-red learn">Learn More <svg width="8" height="12" viewBox="0 0 8 12"><polyline points="2,1 7,6 2,11" fill="none" stroke="#fff" stroke-width="2"/></svg></div>
</section>

<section class="features">
  <h2 class="abs display">Product Features and Philosophy</h2>
  <div class="abs feature" style="left:145px">
    <div class="ph" role="img" aria-label="Climber helping a partner up a rock at sunset" style="background:linear-gradient(180deg,#e9c49a 0%,#b98a62 55%,#3a2c24 100%)"></div>
    <div class="feature-box">
      <h3>FOCUS ON TOP-TIER EVENTS</h3><hr>
      <p>Annually, we develop high-quality sports travel products centered around the world's international top-tier events, including but not limited to: the Globe Shield Finals, Vantara Games, Royal Quartet Tennis, Continental Nations Cup, and the Harbor Cup.</p>
    </div>
  </div>
  <div class="abs feature" style="left:620px">
    <div class="ph" role="img" aria-label="Golfer finishing a swing under a clear sky" style="background:linear-gradient(180deg,#9fb9d2 0%,#cdd7c4 55%,#7a8f5a 100%)"></div>
    <div class="feature-box">
      <h3>ULTIMATE CLIENT EXPERIENCE</h3><hr>
      <p>We focus on the emotional value of the client's journey and viewing experience, providing one-stop, high-quality service solutions to ensure every trip is a "once-in-a-lifetime unforgettable travel experience." From itinerary planning and securing rare tickets to arranging</p>
    </div>
  </div>
</section>

<section class="products">
  <div class="abs circle-arrow" style="left:146px;top:95px"><svg width="10" height="12" viewBox="0 0 10 12"><polyline points="7,1 2,6 7,11" fill="none" stroke="#333" stroke-width="1.6"/></svg></div>
  <h2 class="abs display">Sports Travel Products</h2>
  <div class="abs circle-arrow" style="left:1022px;top:95px"><svg width="10" height="12" viewBox="0 0 10 12"><polyline points="3,1 8,6 3,11" fill="none" stroke="#333" stroke-width="1.6"/></svg></div>
  <div class="abs product" style="left:10px"><div class="ph" role="img" aria-label="Golden trophy on a pitch with confetti" style="background:linear-gradient(180deg,#b98a8a 0%,#7d6f8e 40%,#5c7a3c 85%,#3e7d2a 100%)"></div><p>GLOBE SHIELD</p></div>
  <div class="abs product" style="left:308px"><div class="ph" role="img" aria-label="Tennis court viewed from the stands" style="background:linear-gradient(180deg,#7eaad8 0%,#3c8ee0 35%,#1b6fc6 65%,#c9b59a 100%)"></div><p class="hl">ROYAL QUARTET</p></div>
  <div class="abs product" style="left:606px"><div class="ph" role="img" aria-label="Games sculpture in front of a mountain stadium" style="background:linear-gradient(180deg,#8f9fa6 0%,#b3b4ae 45%,#9a9d94 65%,#6f8c3e 100%)"></div><p>VANTARA GAMES</p></div>
  <div class="abs product" style="left:904px"><div class="ph" role="img" aria-label="Footballer striking a ball under stadium lights" style="background:linear-gradient(180deg,#1d2a3c 0%,#2b3d55 45%,#2e6a2a 75%,#3d8a30 100%)"></div><p>FOOTBALL</p></div>
</section>

<section class="reviews">
  <h2 class="abs display">Reviews</h2>
  <div class="abs rev-prev"><svg width="10" height="12" viewBox="0 0 10 12"><polyline points="7,1 2,6 7,11" fill="none" stroke="#333" stroke-width="1.6"/></svg></div>
  <div class="abs review" style="left:145px">
    <svg class="quote-mark" viewBox="0 0 60 46"><path d="M4 44V26C4 12 11 4 24 2v8c-7 2-10 6-10 12h10v22zM34 44V26c0-14 7-22 20-24v8c-7 2-10 6-10 12h10v22z" fill="#e2231a"/></svg>
    <p>"Lorem ipsum dolor sit amet, consectetur adipiscing elit, sed do eiusmod tempor incididunt ut labore et dolore magna aliqua. Ut enim ad minim veniam, quis nostrud exercitation ullamco laboris nisi ut aliquip"</p>
    <div class="stars">★★★★★</div>
    <div class="person"><div class="avatar" role="img" aria-label="Reviewer portrait"></div><div><b>John Doe</b><span>Company name</span></div></div>
  </div>
  <div class="abs review" style="left:618px">
    <svg class="quote-mark" viewBox="0 0 60 46"><path d="M4 44V26C4 12 11 4 24 2v8c-7 2-10 6-10 12h10v22zM34 44V26c0-14 7-22 20-24v8c-7 2-10 6-10 12h10v22z" fill="#e2231a"/></svg>
    <p>"Lorem ipsum dolor sit amet, consectetur adipiscing elit, sed do eiusmod tempor incididunt ut labore et dolore magna aliqua. Ut enim ad minim veniam, quis nostrud exercitation ullamco laboris nisi ut aliquip"</p>
    <div class="stars">★★★★★</div>
    <div class="person"><div class="avatar" role="img" aria-label="Reviewer portrait"></div><div><b>John Doe</b><span>Company name</span></div></div>
  </div>
  <div class="abs rev-next"><svg width="10" height="12" viewBox="0 0 10 12"><polyline points="3,1 8,6 3,11" fill="none" stroke="#fff" stroke-width="1.8"/></svg></div>
</section>

<section class="faq">
  <h2 class="abs display">Frequently Asked Questions</h2>
  <div class="abs faq-item" style="left:145px;top:166px"><span>Lorem ipsum dolor sit amet, consectetur?</span><span>+</span></div>
  <div class="abs faq-item" style="left:612px;top:166px"><span>Lorem ipsum dolor sit amet, consectetur?</span><span>+</span></div>
  <div class="abs faq-item" style="left:145px;top:246px"><span>Lorem ipsum dolor sit amet, consectetur?</span><span>+</span></div>
  <div class="abs faq-item" style="left:612px;top:246px"><span>Lorem ipsum dolor sit amet, consectetur?</span><span>+</span></div>
  <div class="abs faq-item" style="left:145px;top:326px"><span>Lorem ipsum dolor sit amet, consectetur?</span><span>+</span></div>
  <div class="abs faq-item" style="left:612px;top:326px"><span>Lorem ipsum dolor sit amet, consectetur?</span><span>+</span></div>
  <div class="abs faq-item" style="left:145px;top:406px"><span>Lorem ipsum dolor sit amet, consectetur?</span><span>+</span></div>
  <div class="abs faq-item" style="left:612px;top:406px"><span>Lorem ipsum dolor sit amet, consectetur?</span><span>+</span></div>
</section>

<section class="contact">
  <h2 class="abs display">Contact Us</h2>
  <div class="ph map" role="img" aria-label="Location map of the central United States">
    <div class="abs map-card">
      <svg class="abs" style="left:12px;top:10px" width="12" height="16" viewBox="0 0 12 16"><path d="M6 0C2.7 0 0 2.6 0 5.8 0 10 6 16 6 16s6-6 6-10.2C12 2.6 9.3 0 6 0z" fill="#e2231a"/><circle cx="6" cy="6" r="2.2" fill="#fff"/></svg>
      123, Lorem ipsum dolor sit<u>View Larger Map</u>
    </div>
  </div>
  <div class="abs field" style="top:154px">Name</div>
  <div class="abs field" style="top:218px">Email address</div>
  <div class="abs field" style="top:282px">Phone</div>
  <div class="abs field" style="top:346px;height:162px">Message</div>
  <div class="abs btn-red submit">Submit Now <svg width="8" height="12" viewBox="0 0 8 12"><polyline points="2,1 7,6 2,11" fill="none" stroke="#fff" stroke-width="2"/></svg></div>
</section>

<section class="gallery">
  <div class="ph g" role="img" aria-label="Youth football players chasing the ball" style="left:0;width:322px;clip-path:polygon(0 0,100% 0,90.7% 100%,0 100%);background:linear-gradient(180deg,#3f6a3a,#5f9a48 60%,#8cc06a)"></div>
  <div class="ph g" role="img" aria-label="Dimmed photo of a runner" style="left:296px;width:318px;clip-path:polygon(9.4% 0,100% 0,90.6% 100%,0 100%);background:linear-gradient(180deg,#2b3028,#3a4034)">
    <svg class="abs" style="left:128px;top:126px" width="62" height="62" viewBox="0 0 62 62"><circle cx="31" cy="31" r="31" fill="#fff"/><path d="M31 23v16M23 31h16" stroke="#333" stroke-width="2"/></svg>
  </div>
  <div class="ph g" role="img" aria-label="Skier carving down a snowy slope" style="left:588px;width:322px;clip-path:polygon(9.3% 0,100% 0,90.7% 100%,0 100%);background:linear-gradient(180deg,#8faecb,#dfe7ee 55%,#f4f6f8)"></div>
  <div class="ph g" role="img" aria-label="Hiker celebrating on a mountain summit" style="left:884px;width:316px;clip-path:polygon(9.5% 0,100% 0,100% 100%,0 100%);background:linear-gradient(180deg,#1d3f7a,#5e7ea8 55%,#a9b8c8)"></div>
</section>

<footer class="footer">
  <h3 class="abs" style="left:143px;top:84px">Newsletter</h3>
  <div class="abs nl-input"><svg width="14" height="11" viewBox="0 0 14 11"><rect x="0.5" y="0.5" width="13" height="10" fill="#fff"/><polyline points="1,1 7,6 13,1" fill="none" stroke="#0d3f8d" stroke-width="1.3"/></svg>Email address</div>
  <div class="abs nl-btn">SUBSCRIBE</div>

  <div class="abs links" style="left:471px;top:84px"><h3>Quick Links</h3>
    <ul><li>Home</li><li>Our Story</li><li>Products</li><li>Resources</li><li>Blog</li><li>Contact</li></ul></div>
  <div class="abs links" style="left:655px;top:84px"><h3>Support</h3>
    <ul><li>Get Involved</li><li>Support</li><li>Terms of Service</li><li>FAQ</li><li>Blog</li><li>Contact</li></ul></div>
  <div class="abs touch" style="left:866px;top:84px"><h3>Get in Touch</h3>
    <ul>
      <li><svg width="12" height="12" viewBox="0 0 12 12"><path d="M2.5 0.5l2 2.5-1.2 1.5c.8 1.7 2 2.9 3.7 3.7L8.5 7l2.5 2-1 2.5C5 11 1 7 .5 2z" fill="#e2231a"/></svg>+1 555 010 2400</li>
      <li><svg width="13" height="10" viewBox="0 0 13 10"><rect width="13" height="10" rx="1" fill="#e2231a"/><polyline points="1,1 6.5,5.5 12,1" fill="none" stroke="#fff" stroke-width="1.2"/></svg>info@peakroamjourneys.example</li>
    </ul></div>
  <div class="abs socials"><i style="background:#fff"></i><i style="background:var(--red);border:2px solid #fff"></i></div>

  <p class="abs copy">© Copyrights 2025 | All Rights Reserved</p>
</footer>

</body>
</html>
```